Hollendorf Business Card

This is the personal business card for Dr Mark Hollendorf and convers three area of his professional activity - all of them involve (foreign) languages:
o QRVB International Ltd - A translation company with 50 staff. Trades internationally
o WideHarbor Ltd - a global online auction marketplace for translation services (startup)
o Tonal Mosaic - cutting edge technology from the brain sciences which helps learners assimilate the sound patterns of a new language (startup)

Target Market(s)

The card needs to have a "cutting edge" feel - but for a fairly conservative audience - academics, investors.

Industry/Entity Type

Business

Requirements
Must have
• Text:
Dr Mark Hollendorf

Co-founder QRVB International Ltd (Language translation)
Founder WideHarbor Ltd (Translation marketplace)
Founder Tonal Mosaic (Language acquisition)

email: mark.oswin@velmora.co.nz
Phone: +64 21 596 3172
Twitter: @MarkOswin7

```html
<!DOCTYPE html>
<html lang="en">
<head>
<meta charset="utf-8">
<title>Dr Mark Hollendorf – Business Card</title>
<link rel="stylesheet" href="https://fonts.googleapis.com/css2?family=Tinos&family=Pathway+Gothic+One&display=swap">
<style>
  :root {
    --ink: #000000;
    --paper: #ffffff;
    --text: #1a1a1a;
  }
  html, body {
    margin: 0;
    padding: 0;
    overflow: hidden;
    background: var(--paper);
  }
  .card {
    position: relative;
    width: 1200px;
    height: 686px;
    background: var(--paper);
    overflow: hidden;
  }
  .card__frame {
    position: absolute;
    inset: 0;
  }
  .card__title {
    position: absolute;
    left: 103px;
    top: 128px;
    margin: 0;
    font-family: "Tinos", "Times New Roman", serif;
    font-weight: 400;
    font-size: 47px;
    color: var(--paper);
    white-space: nowrap;
  }
  .ventures {
    position: absolute;
    left: 112px;
    top: 322px;
    margin: 0;
    padding: 0;
    list-style: none;
    font-family: "Pathway Gothic One", "Arial Narrow", sans-serif;
    font-size: 19px;
    color: var(--text);
  }
  .ventures li {
    height: 59px;
    white-space: nowrap;
  }
  .contact {
    position: absolute;
    left: 112px;
    top: 500px;
    font-family: "Pathway Gothic One", "Arial Narrow", sans-serif;
    font-size: 26px;
    line-height: 41px;
    color: var(--text);
    font-style: normal;
  }
  .contact p { margin: 0; white-space: nowrap; }
  .profile {
    position: absolute;
    left: 695px;
    top: 340px;
    width: 500px;
  }
  .profile__name {
    margin: 0;
    font-family: "Tinos", "Times New Roman", serif;
    font-weight: 700;
    font-size: 37px;
    line-height: 1;
    color: var(--text);
    padding-bottom: 20px;
    border-bottom: 2px solid var(--ink);
  }
  .profile__role {
    margin: 22px 0 0;
    font-family: "Tinos", "Times New Roman", serif;
    font-size: 30px;
    line-height: 40px;
    color: var(--text);
    text-transform: uppercase;
  }
</style>
</head>
<body>
<main class="card">
  <svg class="card__frame" width="1200" height="686" viewBox="0 0 1200 686" aria-hidden="true">
    <rect class="title-block" x="70" y="32" width="544" height="250" fill="var(--ink)"/>
    <rect class="rule-top" x="18" y="55" width="1182" height="6" fill="var(--ink)"/>
    <rect class="rule-top-inset" x="70" y="55" width="544" height="6" fill="var(--paper)"/>
    <rect class="rule-side" x="54" y="32" width="4" height="620" fill="var(--ink)"/>
    <rect class="rule-side-inset" x="84" y="32" width="4" height="250" fill="var(--paper)"/>
  </svg>

  <h1 class="card__title">Dr. Mark Hollendorf</h1>

  <ul class="ventures">
    <li>Co-founder QRVB International Ltd (Language Translation)</li>
    <li>Founder WideHarbor Ltd (Translation Marketplace)</li>
    <li>Founder Tonal Mosaic (Language Acquisition)</li>
  </ul>

  <address class="contact">
    <p>Phone: +64 21 596 3172</p>
    <p>Twitter: @MarkOswin7</p>
    <p>E-mail: mark.oswin@velmora.co.nz</p>
  </address>

  <section class="profile">
    <h2 class="profile__name">Mark Hollendorf</h2>
    <p class="profile__role">Profession in foreign<br>languages</p>
  </section>
</main>
</body>
</html>
```